e-commerce store for sport clothing online store "baseball merchandise "web application...

I want to design a UX/UI for my web application website for the online store I will provide you with the following:
1. screen shots of the initial design for the pages>
2. the logo files.
3. The brand guideline file.

the provided files (screen shots) is guideline I want to see CREATIVITY with the UX/UI DESIGN.
PS. PLEASE FOLLOW THE BRANDGUIDE LINE CAREFULLY SPECIALLY THE TYPOGRAPHY & THE COLOR CODES.

PLEASE VISIT THIS WEBSITE brightlane.varomi-qz.com to see more for the screens.

```html
<!DOCTYPE html>
<html lang="en">
<head>
<meta charset="utf-8">
<title>Checkout – Shipping Details</title>
<link rel="stylesheet" href="https://fonts.googleapis.com/css2?family=Lato:wght@400;700;900&display=swap">
<style>
  :root {
    --navy: #0c2340;
    --white: #ffffff;
    --ink: #111111;
    --field-border: #2b2b2b;
    --label: #555555;
    --placeholder: #4a4a4a;
    --button-disabled: #9b9b9b;
    --page: #ffffff;
  }
  * { box-sizing: border-box; margin: 0; padding: 0; }
  html, body {
    width: 1200px;
    height: 3017px;
    overflow: hidden;
    background: var(--page);
    font-family: "Lato", sans-serif;
  }
  .screen {
    position: absolute;
    top: 0; left: 0;
    width: 360px;
    height: 905px;
    transform: scale(3.33334);
    transform-origin: 0 0;
    background: var(--page);
  }
  .app-bar {
    position: absolute; left: 0; top: 0;
    width: 360px; height: 80px;
    background: var(--navy);
  }
  .app-bar .back {
    position: absolute; left: 23px; top: 31px;
    width: 18px; height: 18px;
  }
  .app-bar .title {
    position: absolute; left: 0; right: 0; top: 30px;
    text-align: center; color: var(--white);
    font-weight: 900; font-size: 16px; line-height: 20px;
  }
  .stepper { position: absolute; left: 0; top: 0; width: 360px; height: 200px; }
  .stepper .link {
    position: absolute; top: 137px; height: 1px; background: var(--navy);
  }
  .step-dot {
    position: absolute; top: 118px;
    width: 38px; height: 38px; border-radius: 50%;
    border: 1.5px solid var(--navy);
    background: var(--white); color: var(--navy);
    font-weight: 900; font-size: 18px;
    display: flex; align-items: center; justify-content: center;
  }
  .step-dot.is-active { background: var(--navy); color: var(--white); }
  .step-label {
    position: absolute; top: 162px; width: 100px;
    text-align: center; color: var(--navy);
    font-size: 12px; line-height: 15px;
  }
  .section-title {
    position: absolute; left: 14px;
    font-weight: 700; font-size: 15px; color: var(--ink);
  }
  .field {
    position: absolute; height: 47px;
    border: 1px solid var(--field-border); border-radius: 5px;
    background: var(--white);
  }
  .field .label {
    position: absolute; left: 10px; top: 6px;
    font-size: 11px; color: var(--label);
  }
  .field .value {
    position: absolute; left: 10px; top: 21px;
    font-size: 15px; color: var(--ink);
  }
  .field .placeholder {
    position: absolute; left: 10px; top: 14px;
    font-size: 14px; color: var(--placeholder);
  }
  .action-bar {
    position: absolute; left: 5px; top: 742px;
    width: 350px; height: 58px;
    background: var(--white); border-radius: 10px;
    box-shadow: 0 1px 6px rgba(0,0,0,0.28);
  }
  .proceed-button {
    position: absolute; left: 7px; top: 7px;
    width: 337px; height: 44px;
    border: none; border-radius: 6px;
    background: var(--button-disabled); color: var(--white);
    font-family: "Lato", sans-serif; font-weight: 700; font-size: 13px;
  }
</style>
</head>
<body>
<main class="screen">
  <header class="app-bar">
    <svg class="back" viewBox="0 0 18 18" aria-hidden="true">
      <path d="M17 9H2M8.5 2.5L2 9l6.5 6.5" fill="none" stroke="#ffffff" stroke-width="2" stroke-linecap="round" stroke-linejoin="round"/>
    </svg>
    <h1 class="title">Checkout</h1>
  </header>

  <nav class="stepper" aria-label="Checkout progress">
    <span class="link" style="left:98px;width:63px"></span>
    <span class="link" style="left:199px;width:63px"></span>
    <span class="step-dot is-active" style="left:60px">1</span>
    <span class="step-dot" style="left:161px">2</span>
    <span class="step-dot" style="left:262px">3</span>
    <span class="step-label" style="left:29px">Shipping<br>Details</span>
    <span class="step-label" style="left:130px">Payment<br>Details</span>
    <span class="step-label" style="left:231px">Confirmation</span>
  </nav>

  <h2 class="section-title" style="top:221px">Deliver to</h2>
  <div class="field" style="left:14px;top:255px;width:158px"><span class="label">First Name*</span><span class="value">Rafi</span></div>
  <div class="field" style="left:187px;top:255px;width:158px"><span class="label">Last Name*</span><span class="value">Delmar</span></div>
  <div class="field" style="left:14px;top:319px;width:331px"><span class="label">Phone*</span><span class="value">58019273xx</span></div>

  <h2 class="section-title" style="top:397px">Shipping Address</h2>
  <div class="field" style="left:14px;top:431px;width:331px"><span class="placeholder">Area*</span></div>
  <div class="field" style="left:14px;top:495px;width:158px"><span class="placeholder">Block*</span></div>
  <div class="field" style="left:187px;top:495px;width:158px"><span class="placeholder">Street*</span></div>
  <div class="field" style="left:14px;top:559px;width:158px"><span class="placeholder">Avenue</span></div>
  <div class="field" style="left:187px;top:559px;width:158px"><span class="placeholder">Building</span></div>
  <div class="field" style="left:14px;top:623px;width:158px"><span class="placeholder">Floor</span></div>
  <div class="field" style="left:187px;top:623px;width:158px"><span class="placeholder">Appartment</span></div>
  <div class="field" style="left:14px;top:687px;width:331px"><span class="placeholder">Map Location</span></div>

  <div class="action-bar">
    <button class="proceed-button" type="button" disabled>Proceed</button>
  </div>
</main>
</body>
</html>
```